A fantastic website for a physio

We are looking for an eye catching website which can attract as many customer as possible.
We have logo designed and ready to be used in the website.
Please use the green and blue which is used in our logo for the preferred colors.
The following are the designs that I Iike:
http://www.example-clinicone.com.au/
http://www.example-rehabtwo.com.au/
We will be having other services including massage therapy, Psychology and podiatrist. You can find information about podiatry in our condition sheet.
for the address you can put Shop 5/248 Wattlebrook Street, Kelvindale. It might change but for now you can leave it until I confirm that in the next couple of days.

Logo file can be downloaded here:
https://files.example-share.net/s/qz4mtl9wkr82bvx/Logo1511.jpg?dl=0

Target Market(s)

Infant to old people.
We speak Farsi.

Industry/Entity Type

Physical Therapy

Number of Pages Required

5+ page

Font styles to use
Serif

Colors
33a6d7
abd037
e667a6

Requirements
Must have
• Home, About , our services, Conditions we treat and contact
• For home page and contacts we would like a tab that can connect to another website(bookwell) for online booking. We would like the patient's to be able to leave us massage or leave their email for monthly news letter. For the condition we treat you can use the condition sheets I have attached. For about us and home page you can use brochure I have attached.
• The other things should have include: in-line contact form, Google Map, clinic hours, newsletter sign-up etc, schema rich contact information
• Social media connection to our Facebook, Instagram and linked in
Nice to have
• Search engine optimization for Merrylands and Parramatta physiotherapy.
• We can speak English and Farsi. So is nice to have an information tab for Farsi speaking people. I can provide you with the texts.

```html
<!DOCTYPE html>
<html lang="en">
<head>
<meta charset="utf-8">
<title>Harbourline Physiotherapy</title>
<link rel="stylesheet" href="https://fonts.googleapis.com/css2?family=Poiret+One&family=Roboto:wght@300;400;500;700&display=swap">
<style>
:root{
  --blue:#33a6d7;
  --blue-dark:#1f8fc4;
  --green:#8dc63f;
  --green-light:#abd037;
  --pink:#e667a6;
  --grey:#ececec;
  --text:#444;
  --muted:#666;
  --white:#fff;
}
*{margin:0;padding:0;box-sizing:border-box}
html,body{width:1200px;height:3291px;overflow:hidden;background:var(--white)}
body{font-family:"Roboto",sans-serif;color:var(--text);position:relative}
.page{position:relative;width:1200px;height:3291px;overflow:hidden}
.abs{position:absolute}

/* top bar */
.topbar{left:0;top:0;width:1200px;height:35px;background:var(--green);color:var(--white);font-size:14px}
.topbar .contact{left:100px;top:9px;display:flex;gap:34px}
.topbar .lang{left:834px;top:7px;display:flex;align-items:center;gap:8px}
.flag{width:34px;height:20px;background:#2b4a9b;border:1px solid #fff}
.topbar .social{left:990px;top:10px;display:flex;gap:10px}
.dot{width:14px;height:14px;border-radius:50%;background:var(--white)}

/* header */
.header{left:0;top:35px;width:1200px;height:101px;background:var(--white)}
.brand{left:98px;top:22px;display:flex;align-items:center;gap:12px}
.brand .mark{width:58px;height:58px;border-radius:50%;background:var(--blue)}
.brand .name{font-family:"Roboto",sans-serif;font-weight:700;font-size:27px;color:var(--blue);line-height:1.05}
.nav{left:500px;top:52px;display:flex;font-size:16px;font-weight:500;color:#222}
.nav a{color:inherit;text-decoration:none;padding:0 22px;position:relative}
.nav a.active{color:var(--blue)}
.nav a.active::after{content:"";position:absolute;left:22px;right:22px;bottom:-14px;height:3px;background:var(--blue)}
.nav .home-icon{position:absolute;left:36px;top:-26px;width:18px;height:18px;border-radius:50%;background:var(--green)}

/* hero */
.hero{left:0;top:136px;width:1200px;height:522px;background:linear-gradient(100deg,#4fb8df 0%,#3ea7c9 35%,#5fb27a 65%,#7fbf4a 100%)}
.hero-title{left:100px;top:270px;width:556px;height:60px;background:var(--green);color:var(--white);font-family:"Poiret One",sans-serif;font-size:38px;font-weight:400;line-height:60px;padding-left:12px}
.hero-text{left:100px;top:345px;width:560px;color:var(--white);font-size:17px;line-height:1.6}
.btn{display:inline-block;color:var(--white);font-size:15px;text-align:center;border:none}
.hero-btn{left:100px;top:432px;width:124px;height:48px;line-height:48px;background:var(--green);border:1px solid #fff}
.appt{left:761px;top:182px;width:336px;height:415px;background:var(--blue);border:3px solid var(--white);color:var(--white);padding:18px 20px}
.appt h2{font-size:26px;font-weight:500;text-align:center;border-bottom:2px solid rgba(255,255,255,.8);padding-bottom:14px}
.appt p{font-size:21px;text-align:center;margin:22px 0 24px}
.field{height:40px;border:2px solid var(--white);border-radius:4px;font-size:14px;color:var(--white);line-height:36px;padding-left:10px;margin-bottom:11px;background:rgba(255,255,255,.08)}
.appt .btn{width:100%;height:40px;line-height:40px;background:var(--green);border-radius:4px;margin-top:10px;font-weight:700}

/* section heading */
.heading{left:0;width:1200px;text-align:center;font-family:"Poiret One",sans-serif;font-size:42px;color:var(--blue)}
.heading span{color:var(--green)}
.divider{left:0;width:1200px;display:flex;justify-content:center;align-items:center;gap:10px}
.divider i{display:block;width:140px;height:2px;background:var(--blue)}
.divider b{display:block;width:32px;height:32px;border-radius:50%;background:var(--green);border:4px solid var(--blue)}

.welcome{left:128px;top:832px;width:944px;text-align:center;font-size:13.5px;line-height:25px;color:var(--text)}

/* services */
.service{width:330px;text-align:center}
.service h3{font-family:"Poiret One",sans-serif;font-weight:400;font-size:30px;margin:16px 0 12px}
.service p{font-size:13.5px;line-height:25px;color:var(--text);padding:0 20px}
.ring{margin:0 auto;width:196px;height:196px}

/* therapies */
.grey{left:0;top:1426px;width:1200px;height:658px;background:var(--grey)}
.card{top:1597px;width:320px;height:444px;background:var(--white);border:1px solid #ddd;text-align:center}
.card .photo{height:220px;background:linear-gradient(135deg,#d9c3a8,#b9cfd8)}
.card h3{color:var(--blue);font-size:24px;font-weight:500;margin:22px 0 10px}
.card p{font-size:13px;line-height:25px;padding:0 10px;color:var(--text)}
.card .btn{margin-top:18px;width:104px;height:42px;line-height:42px;background:var(--blue);border-radius:3px}
.card svg{position:absolute;left:0;top:0}

/* quick contact */
.quick{left:0;top:2084px;width:1200px;height:356px;background:var(--pink);border-top:6px solid #f08cbf}
.qfield{height:40px;border:2px solid rgba(255,255,255,.8);background:rgba(255,255,255,.25);color:var(--white);font-size:14px;line-height:36px;padding-left:10px}
.quick-btn{left:459px;top:2345px;width:285px;height:42px;line-height:38px;background:var(--blue);border:2px solid var(--white);font-weight:500}

/* testimonials */
.avatar{width:110px;height:110px;border-radius:50%;border:3px solid var(--blue);background:radial-gradient(circle,#f0d9c4,#c9a77e)}
.quote{font-family:Georgia,serif;font-size:60px;color:var(--green);line-height:1}
.t-title{font-size:17px;font-weight:500;color:#333}
.t-name{font-size:15px;color:var(--muted);margin-top:8px}
.stars{color:var(--green);font-size:16px;margin-top:8px;letter-spacing:2px}
.t-text{font-size:13.5px;line-height:22px;color:var(--muted);width:530px}

/* footer */
.footer{left:0;top:2830px;width:1200px;height:400px;background:var(--blue);color:var(--white)}
.fcol h4{font-size:17px;font-weight:500;margin-bottom:10px}
.fcol h4::after{content:"";display:block;width:72px;height:2px;background:var(--white);margin-top:10px}
.hours{font-size:13px;line-height:33px;display:grid;grid-template-columns:110px 1fr}
.citem{display:flex;gap:14px;margin-bottom:14px;font-size:13px;line-height:20px}
.citem .ic{flex:none;width:36px;height:36px;border-radius:50%;border:2px solid var(--white)}
.citem strong{font-weight:700;display:block}
.nfield{width:210px;height:34px;border:2px solid var(--white);font-size:13px;line-height:30px;padding-left:10px;margin-bottom:10px}
.nbtn{width:120px;height:38px;line-height:38px;background:var(--green);font-weight:700;font-size:13px}
.map{left:808px;top:2954px;width:292px;height:235px;background:linear-gradient(135deg,#eef1e6,#dfe6ea);border:4px solid var(--white)}
.bottombar{left:0;top:3230px;width:1200px;height:61px;background:var(--green);color:var(--white);font-size:14px}
.bottombar .copy{left:100px;top:22px}
.bottombar .social{left:946px;top:14px;display:flex;gap:8px}
.bottombar .social span{width:34px;height:34px;border:2px solid var(--white);border-radius:50%}
</style>
</head>
<body>
<div class="page">

  <div class="abs topbar">
    <div class="abs contact"><span>&#9742; +61.400555018</span><span>&#9679; 12/7 Ferncourt Avenue, Kelvindale NSW 2190</span></div>
    <div class="abs lang"><span class="flag"></span><span>Lan: Eng &#9662;</span></div>
    <div class="abs social"><span class="dot"></span><span class="dot"></span><span class="dot"></span><span class="dot"></span><span class="dot"></span></div>
  </div>

  <header class="abs header">
    <div class="abs brand">
      <span class="mark"></span>
      <div class="name">Harbourline<br>Physiotherapy</div>
    </div>
    <nav class="abs nav">
      <a class="active" href="#"><span class="home-icon"></span>HOME</a>
      <a href="#">ABOUT US</a>
      <a href="#">SERVICES</a>
      <a href="#">CONDITIONS WE TREAT</a>
      <a href="#">CONTACT</a>
    </nav>
  </header>

  <section class="abs hero" role="img" aria-label="Physiotherapist treating a patient in a clinic room, blue to green tint"></section>
  <svg class="abs" style="left:0;top:560px" width="1200" height="110" viewBox="0 0 1200 110" aria-hidden="true">
    <path d="M0 70 Q600 -10 1200 40 L1200 110 L0 110Z" fill="#fff"/>
    <path d="M0 78 Q600 0 1200 30 L1200 44 Q600 14 0 92Z" fill="var(--green)"/>
  </svg>
  <h1 class="abs hero-title">HARBOURLINEPHYSIOTHERAPY</h1>
  <p class="abs hero-text">We help you learn to work with your body to restore mobility through concentrated, specialized exercises and stretches.</p>
  <a class="abs btn hero-btn">Read More</a>

  <form class="abs appt">
    <h2>APPOINTMENT FORM</h2>
    <p>Get Your Appointment Today!</p>
    <div class="field">Name</div>
    <div class="field">Mobile Phone</div>
    <div class="field">Email</div>
    <div class="field">Appointment Type</div>
    <div class="btn">GET APPOINTMENT</div>
  </form>

  <h2 class="abs heading" style="top:710px">Welcome To <span>Harbourline Physiotherapy</span></h2>
  <div class="abs divider" style="top:770px"><i></i><b></b><i></i></div>
  <p class="abs welcome">Our aim at Harbourline Physiotherapy is the comprehensive delivery of the highest quality of care for those suffering from pain and/or stress. We are dedicated to producing the results that you are committed to achieving. Our clinic has been trusted in the community for over 30 years and our skilled professionals offer you a variety of treatment methods to help restore and maintain optimal physical function and mobility. We look forward to providing you with care, support and understanding to make this an environment that will nurture your ability to achieve your goal.</p>

  <h2 class="abs heading" style="top:958px">Our <span>Services</span></h2>
  <div class="abs divider" style="top:1014px"><i></i><b></b><i></i></div>

  <div class="abs service" style="left:90px;top:1053px">
    <svg class="ring" viewBox="0 0 196 196" role="img" aria-label="Massage therapy icon">
      <path d="M98 6 A92 92 0 0 1 190 98" stroke="var(--green)" stroke-width="10" fill="none"/>
      <path d="M98 190 A92 92 0 0 1 6 98" stroke="var(--green)" stroke-width="10" fill="none"/>
      <path d="M6 98 A92 92 0 0 1 98 6" stroke="var(--blue)" stroke-width="10" fill="none"/>
      <path d="M190 98 A92 92 0 0 1 98 190" stroke="var(--blue)" stroke-width="10" fill="none"/>
      <circle cx="98" cy="98" r="74" fill="var(--blue)"/>
    </svg>
    <h3 style="color:var(--blue)">Massage Therapy</h3>
    <p>We believe that during rehabilitation, the patient should be educated by their therapist in order to be able to maintain maximum flexibility.</p>
  </div>
  <div class="abs service" style="left:435px;top:1053px">
    <svg class="ring" viewBox="0 0 196 196" role="img" aria-label="Psychology therapy icon">
      <path d="M98 6 A92 92 0 0 1 190 98" stroke="var(--blue)" stroke-width="10" fill="none"/>
      <path d="M98 190 A92 92 0 0 1 6 98" stroke="var(--blue)" stroke-width="10" fill="none"/>
      <path d="M6 98 A92 92 0 0 1 98 6" stroke="var(--green)" stroke-width="10" fill="none"/>
      <path d="M190 98 A92 92 0 0 1 98 190" stroke="var(--green)" stroke-width="10" fill="none"/>
      <circle cx="98" cy="98" r="74" fill="var(--green)"/>
    </svg>
    <h3 style="color:var(--green)">Psychology Therapy</h3>
    <p>We believe that during rehabilitation, the patient should be educated by their therapist in order to be able to maintain maximum flexibility.</p>
  </div>
  <div class="abs service" style="left:780px;top:1053px">
    <svg class="ring" viewBox="0 0 196 196" role="img" aria-label="Podiatrist therapy icon">
      <path d="M98 6 A92 92 0 0 1 190 98" stroke="var(--green)" stroke-width="10" fill="none"/>
      <path d="M98 190 A92 92 0 0 1 6 98" stroke="var(--green)" stroke-width="10" fill="none"/>
      <path d="M6 98 A92 92 0 0 1 98 6" stroke="var(--blue)" stroke-width="10" fill="none"/>
      <path d="M190 98 A92 92 0 0 1 98 190" stroke="var(--blue)" stroke-width="10" fill="none"/>
      <circle cx="98" cy="98" r="74" fill="var(--pink)"/>
    </svg>
    <h3 style="color:var(--pink)">Podiatrist Therapy</h3>
    <p>We believe that during rehabilitation, the patient should be educated by their therapist in order to be able to maintain maximum flexibility.</p>
  </div>

  <section class="abs grey"></section>
  <h2 class="abs heading" style="top:1448px">Our New <span>Therapies</span></h2>
  <div class="abs divider" style="top:1505px"><i></i><b></b><i></i></div>

  <article class="abs card" style="left:105px">
    <div class="photo" role="img" aria-label="Senior patient doing a stretching exercise on a mat"></div>
    <svg width="320" height="60" viewBox="0 0 320 60" aria-hidden="true"><path d="M0 0 H320 V20 Q160 -10 0 58Z" fill="var(--green)"/><path d="M0 0 H320 V12 Q160 -16 0 44Z" fill="#fff"/></svg>
    <h3>Back Pain</h3>
    <p>In most cases back pain can be treated with activity modification and physiotherapy. In the physiotherapy examination a subjective evaluation.</p>
    <span class="btn">Read More</span>
  </article>
  <article class="abs card" style="left:447px">
    <div class="photo" role="img" aria-label="Therapist treating a patient's neck and shoulders"></div>
    <svg width="320" height="60" viewBox="0 0 320 60" aria-hidden="true"><path d="M0 0 H320 V20 Q160 -10 0 58Z" fill="var(--green)"/><path d="M0 0 H320 V12 Q160 -16 0 44Z" fill="#fff"/></svg>
    <h3>Neck Pain</h3>
    <p>In most cases back pain can be treated with activity modification and physiotherapy. In the physiotherapy examination a subjective evaluation.</p>
    <span class="btn">Read More</span>
  </article>
  <article class="abs card" style="left:782px">
    <div class="photo" role="img" aria-label="Patient exercising with a light dumbbell beside a therapist"></div>
    <svg width="320" height="60" viewBox="0 0 320 60" aria-hidden="true"><path d="M0 0 H320 V20 Q160 -10 0 58Z" fill="var(--green)"/><path d="M0 0 H320 V12 Q160 -16 0 44Z" fill="#fff"/></svg>
    <h3>The Pelvic Floor</h3>
    <p>In most cases back pain can be treated with activity modification and physiotherapy. In the physiotherapy examination a subjective evaluation.</p>
    <span class="btn">Read More</span>
  </article>

  <section class="abs quick" role="img" aria-label="Soft pink tinted background of a treatment session"></section>
  <h2 class="abs heading" style="top:2124px;color:var(--white)">Quick Contact Form</h2>
  <div class="abs qfield" style="left:165px;top:2216px;width:283px">Name</div>
  <div class="abs qfield" style="left:456px;top:2216px;width:286px">Email</div>
  <div class="abs qfield" style="left:750px;top:2216px;width:286px">Telephone</div>
  <div class="abs qfield" style="left:165px;top:2275px;width:283px">Postal Code</div>
  <div class="abs qfield" style="left:456px;top:2275px;width:286px">Treatment <span style="float:right;margin-right:12px">&#9662;</span></div>
  <div class="abs qfield" style="left:750px;top:2275px;width:286px">Message</div>
  <span class="abs btn quick-btn">CONTACT WITH US</span>

  <h2 class="abs heading" style="top:2462px">Patient <span>Testimonials</span></h2>
  <div class="abs divider" style="top:2522px"><i></i><b></b><i></i></div>

  <div class="abs avatar" style="left:127px;top:2600px" role="img" aria-label="Patient portrait"></div>
  <div class="abs quote" style="left:265px;top:2572px">&ldquo;</div>
  <div class="abs" style="left:306px;top:2618px"><div class="t-title">GOOD TREATMENT</div><div class="t-name">Mirela</div><div class="stars">&#9733;&#9733;&#9733;&#9733;&#9734;</div></div>
  <p class="abs t-text" style="left:100px;top:2742px">Neque porro quisquam est, qui dolorem ipsum quia dolor sit amet, consectetur, adipisci velit, sed quia non numquam eius modi tempora.</p>

  <div class="abs avatar" style="left:667px;top:2600px" role="img" aria-label="Patient portrait"></div>
  <div class="abs quote" style="left:805px;top:2572px">&ldquo;</div>
  <div class="abs" style="left:846px;top:2618px"><div class="t-title">GOOD REHABILITATION CLINIC</div><div class="t-name">Soraya</div><div class="stars">&#9733;&#9733;&#9733;&#9733;&#9734;</div></div>
  <p class="abs t-text" style="left:640px;top:2742px">Neque porro quisquam est, qui dolorem ipsum quia dolor sit amet, consectetur, adipisci velit, sed quia non numquam eius modi tempora.</p>

  <footer class="abs footer"></footer>
  <svg class="abs" style="left:0;top:2810px" width="1200" height="110" viewBox="0 0 1200 110" aria-hidden="true">
    <path d="M0 0 H1200 V60 Q600 -10 0 70Z" fill="#fff"/>
    <path d="M0 70 Q600 -10 1200 60 L1200 48 Q600 -20 0 56Z" fill="var(--green)"/>
  </svg>

  <div class="abs fcol" style="left:100px;top:2940px;width:220px;color:#fff">
    <h4>CLINIC HOURS</h4>
    <div class="hours">
      <span>Monday</span><span>7:00 AM - 7:00 PM</span>
      <span>Tuesday</span><span>7:00 AM - 7:00 PM</span>
      <span>Wednesday</span><span>7:00 AM - 7:00 PM</span>
      <span>Thursday</span><span>7:00 AM - 7:00 PM</span>
      <span>Friday</span><span>7:00 AM - 7:00 PM</span>
      <span>Saturday</span><span>8:00 AM - 1:00 PM</span>
    </div>
  </div>
  <div class="abs fcol" style="left:342px;top:2940px;width:215px;color:#fff">
    <h4>CONTACT US</h4>
    <div class="citem" style="margin-top:14px"><span class="ic"></span><div><strong>ADDRESS,</strong>9 Orchard Lane, Kelvindale, New South Wales</div></div>
    <div class="citem"><span class="ic"></span><div><strong>PHONE:</strong>+61.400555018</div></div>
    <div class="citem"><span class="ic"></span><div><strong>Mail:</strong>hello@harbourline.example</div></div>
  </div>
  <div class="abs fcol" style="left:565px;top:2940px;width:220px;color:#fff">
    <h4>NEWSLETTER SIGN-UP</h4>
    <div class="nfield" style="margin-top:14px">Name</div>
    <div class="nfield">Phone</div>
    <div class="nfield">Email</div>
    <div class="btn nbtn">SIGNUP NOW</div>
  </div>
  <div class="abs map" role="img" aria-label="Street map showing the clinic location"></div>

  <div class="abs bottombar">
    <span class="abs copy">Copyright &copy; 2016 Harbourline Physiotherapy. All Right Reserved</span>
    <div class="abs social"><span></span><span></span><span></span><span></span></div>
  </div>

</div>
</body>
</html>
```